Card design for orthopaedic surgeons working as The Brightwater Joint Centre

Business cards, letterhead

Colors

Designer to choose colors to be used in the design.

Requirements
Must have
• Late addition.
• Cards letterhead must have logos of
• Crestmoor Lindell College of Surgeons
• Varenwood Bone Health Association
Nice to have
• Back of card to have space for appointment time to be added by hand and some blank space for writing incidental other notes.

```html
<!DOCTYPE html>
<html lang="en">
<head>
<meta charset="utf-8">
<title>The Brightwater Joint Centre – Business Card</title>
<link rel="stylesheet" href="https://fonts.googleapis.com/css2?family=Montserrat:wght@300;400&family=Open+Sans:wght@400;700&display=swap">
<style>
  :root {
    --navy: #07334d;
    --sky: #2ea8ef;
    --white: #ffffff;
    --ink: #0b3954;
    --backdrop: #e9ecef;
  }
  * { margin: 0; padding: 0; box-sizing: border-box; }
  html, body { width: 1200px; height: 960px; overflow: hidden; }
  body {
    background: var(--backdrop);
    position: relative;
    font-family: "Open Sans", Arial, sans-serif;
  }
  .card {
    position: absolute;
    left: 250px;
    width: 700px;
    height: 400px;
    overflow: hidden;
    box-shadow: 0 6px 18px rgba(0,0,0,0.18);
  }

  /* Back of card */
  .card-back { top: 50px; background: var(--navy); }
  .card-back .brand-name {
    position: absolute;
    top: 150px; left: 0; right: 0;
    text-align: center;
    font-family: "Montserrat", Arial, sans-serif;
    font-weight: 300;
    font-size: 36px;
    color: var(--sky);
    letter-spacing: -0.5px;
    white-space: nowrap;
  }
  .card-back .website {
    position: absolute;
    top: 215px; left: 0; right: 0;
    text-align: center;
    font-size: 18px;
    letter-spacing: 3px;
    color: var(--white);
    white-space: nowrap;
  }
  .card-back .website .domain { color: var(--sky); }

  /* Front of card */
  .card-front { top: 510px; background: var(--white); }
  .card-front .arc-shapes { position: absolute; inset: 0; }
  .card-front .brand-name {
    position: absolute;
    top: 150px; left: 26px;
    font-family: "Montserrat", Arial, sans-serif;
    font-weight: 400;
    font-size: 20px;
    color: var(--ink);
    letter-spacing: -0.3px;
    white-space: nowrap;
  }
  .contact {
    position: absolute;
    top: 72px; right: 30px;
    text-align: right;
    color: var(--white);
    white-space: nowrap;
  }
  .contact .person-name { font-weight: 700; font-size: 24px; line-height: 1.2; }
  .contact .person-title { font-size: 18px; margin-bottom: 14px; }
  .contact .line {
    font-size: 16px;
    line-height: 1.55;
    display: flex;
    justify-content: flex-end;
    align-items: center;
    gap: 8px;
  }
  .contact .icon { width: 14px; height: 14px; flex: none; }
  .contact .address { font-size: 16px; line-height: 1.4; margin-top: 8px; padding-right: 22px; }
</style>
</head>
<body>

  <section class="card card-back" aria-label="Business card back">
    <div class="brand-name">The Brightwater Joint Centre</div>
    <div class="website">www.<span class="domain">brightwaterjoint</span>.com</div>
  </section>

  <section class="card card-front" aria-label="Business card front">
    <svg class="arc-shapes" viewBox="0 0 700 400" width="700" height="400" aria-hidden="true">
      <circle cx="668" cy="300" r="336" fill="var(--sky)"/>
      <circle cx="674" cy="300" r="328" fill="var(--white)"/>
      <circle cx="680" cy="300" r="320" fill="var(--navy)"/>
    </svg>

    <div class="brand-name">The Brightwater Joint Centre</div>

    <div class="contact">
      <div class="person-name">Maren Ashdale</div>
      <div class="person-title">Title</div>
      <div class="line">012-345-6789
        <svg class="icon" viewBox="0 0 16 16"><circle cx="8" cy="8" r="7.5" fill="none" stroke="#fff" stroke-width="1"/><path d="M5 4.5l1.5-.5 1 2-1 .8c.4 1 1.1 1.7 2 2l.8-1 2 1-.5 1.5c-3 .2-6-2.8-5.8-5.8z" fill="#fff"/></svg>
      </div>
      <div class="line">info@brightwaterjoint.com
        <svg class="icon" viewBox="0 0 16 16"><circle cx="8" cy="8" r="7.5" fill="none" stroke="#fff" stroke-width="1"/><rect x="4" y="5" width="8" height="6" fill="#fff"/><path d="M4 5l4 3.2L12 5" fill="none" stroke="var(--navy)" stroke-width="1"/></svg>
      </div>
      <div class="line">www.brightwaterjoint.com
        <svg class="icon" viewBox="0 0 16 16"><circle cx="8" cy="8" r="7" fill="none" stroke="#fff" stroke-width="1.2"/><ellipse cx="8" cy="8" rx="3" ry="7" fill="none" stroke="#fff" stroke-width="1"/><path d="M1 8h14M2.5 4.5h11M2.5 11.5h11" stroke="#fff" stroke-width="1"/></svg>
      </div>
      <div class="address">Street Name, City Name<br>Zipcode - 012345</div>
    </div>
  </section>

</body>
</html>
```